Corporate Template

Looking for a set of corporate slides to be made which contain multiple different slides and orientations. Looking for at least 8 to 10 different master pages plus a Coversheet and closeout page. Incorporating a color palate similar to our logo coloring is preferred.
I have attached a logo.
I like the amber quill works designs best so far. They seem to fit what I'm looking for in terms of visual appearance.
Reason: I'm trying to allow time for a couple new designers to incorporate some changes I requested to their existing designs.

```html
<!DOCTYPE html>
<html lang="en">
<head>
<meta charset="utf-8">
<title>Sample Design 4 – Norvale Neurolabs Presentation Template</title>
<link rel="stylesheet" href="https://fonts.googleapis.com/css2?family=Arimo:wght@400;700&display=swap">
<style>
  :root {
    --brand: #3161a3;
    --brand-dark: #0b2a5c;
    --brand-mid: #2f5fa0;
    --brand-bright: #1d79c4;
    --brand-light: #9cc3ef;
    --sheet: #ffffff;
    --ink: #333333;
    --muted: #9fb3cc;
    --row-a: #d9d9d9;
    --row-b: #ededed;
  }
  * { margin: 0; padding: 0; box-sizing: border-box; }
  html, body { width: 1200px; height: 1000px; overflow: hidden; background: var(--sheet); }
  body { position: relative; font-family: "Arimo", Arial, sans-serif; color: var(--ink); }

  .board-title {
    position: absolute; top: 58px; left: 0; width: 1200px; text-align: center;
    font-size: 28px; font-weight: 700; color: #2a4d85;
  }

  .slide {
    position: absolute; width: 333px; height: 250px; background: var(--sheet);
    overflow: hidden;
  }
  .slide--brand { background: var(--brand); color: #fff; }

  .slide__title {
    position: absolute; left: 33px; top: 16px;
    font-size: 12.5px; font-weight: 700; color: var(--brand);
  }

  .slide__footer {
    position: absolute; left: 0; bottom: 0; width: 100%; height: 20px;
    background: var(--brand);
  }
  .footer-name {
    position: absolute; right: 8px; top: 4px; text-align: right;
    color: #fff; font-size: 7px; font-weight: 700; line-height: 7px; letter-spacing: .3px;
  }
  .footer-name small { display: block; font-size: 3.5px; line-height: 5px; font-weight: 400; letter-spacing: .2px; }

  .cover-name {
    position: absolute; left: 172px; top: 52px; font-size: 31px; line-height: 32px;
    font-weight: 400; letter-spacing: 1px; color: #fff;
  }
  .cover-name small { display: block; font-size: 13.5px; line-height: 20px; letter-spacing: .2px; }
  .cover-heading { position: absolute; right: 18px; bottom: 38px; font-size: 14px; color: #fff; }
  .cover-date { position: absolute; right: 18px; bottom: 22px; font-size: 8.5px; color: var(--muted); }

  .outline { position: absolute; left: 34px; top: 48px; font-size: 9px; line-height: 12px; list-style: none; }
  .outline li.l1::before { content: "• "; color: var(--brand); }
  .outline li.l2 { padding-left: 14px; }
  .outline li.l2::before { content: "– "; }
  .outline li.l3 { padding-left: 26px; }
  .outline li.l3::before { content: "• "; font-size: 7px; }
  .outline li.l4 { padding-left: 38px; }
  .outline li.l4::before { content: "– "; }
  .outline li.l5 { padding-left: 50px; }
  .outline li.l5::before { content: "» "; }

  .chart { position: absolute; left: 0; top: 0; width: 333px; height: 250px; }
  .chart text { font-family: "Arimo", Arial, sans-serif; fill: var(--ink); }

  .data-table {
    position: absolute; left: 17px; top: 62px; width: 296px; border-collapse: collapse;
    font-size: 5.5px; table-layout: fixed;
  }
  .data-table th {
    background: var(--brand); color: #fff; font-weight: 700; height: 14px; font-size: 6.5px;
    border-right: 1px solid #fff; text-align: center;
  }
  .data-table th:first-child { text-align: left; padding-left: 3px; }
  .data-table td { height: 14.5px; text-align: center; border-right: 1px solid #fff; }
  .data-table td:first-child { text-align: left; padding-left: 3px; }
  .data-table tbody tr:nth-child(odd) td { background: var(--row-a); }
  .data-table tbody tr:nth-child(even) td { background: var(--row-b); }

  .blank-label {
    position: absolute; left: 0; width: 100%; top: 114px; text-align: center;
    font-size: 7px; font-weight: 700; color: var(--brand);
  }
</style>
</head>
<body>

<h1 class="board-title">Sample Design 4</h1>

<!-- Cover -->
<section class="slide slide--brand" style="left:25px; top:150px;">
  <div class="cover-name">NORVALE<small>NEUROLABS</small></div>
  <div class="cover-heading">Presentation Template</div>
  <div class="cover-date">October 26, 2013</div>
</section>

<!-- Title and Content -->
<section class="slide" style="left:423px; top:150px;">
  <h2 class="slide__title">Title and Content</h2>
  <ul class="outline">
    <li class="l1">Click to edit Master text styles</li>
    <li class="l2">Second level</li>
    <li class="l3">Third level</li>
    <li class="l4">Fourth level</li>
    <li class="l5">Fifth level</li>
  </ul>
  <footer class="slide__footer"><div class="footer-name">NORVALE<small>NEUROLABS</small></div></footer>
</section>

<!-- Title Only -->
<section class="slide" style="left:825px; top:150px;">
  <h2 class="slide__title">Title Only</h2>
  <footer class="slide__footer"><div class="footer-name">NORVALE<small>NEUROLABS</small></div></footer>
</section>

<!-- Pie Chart -->
<section class="slide" style="left:25px; top:440px;">
  <h2 class="slide__title">Pie Chart</h2>
  <svg class="chart" viewBox="0 0 333 250">
    <text x="166" y="77" font-size="10" font-weight="700" text-anchor="middle">Chart Title</text>
    <g transform="translate(166,155)" stroke="#fff" stroke-width="1.2">
      <path d="M0,0 L0,-53 A53,53 0 1 1 -25.5,46.4 Z" fill="var(--brand-mid)"/>
      <path d="M0,0 L-25.5,46.4 A53,53 0 0 1 -49.3,-19.5 Z" fill="#6a9bd2"/>
      <path d="M0,0 L-49.3,-19.5 A53,53 0 0 1 -28.4,-44.7 Z" fill="var(--brand-light)"/>
      <path d="M0,0 L-28.4,-44.7 A53,53 0 0 1 0,-53 Z" fill="var(--brand-bright)"/>
    </g>
    <g font-size="7">
      <text x="220" y="166">1st Qtr</text><text x="222" y="175">58%</text>
      <text x="90" y="168">2nd Qtr</text><text x="95" y="177">23%</text>
      <text x="103" y="108">3rd Qtr</text><text x="107" y="117">10%</text>
      <text x="140" y="92">4th Qtr</text><text x="145" y="100">9%</text>
    </g>
  </svg>
  <footer class="slide__footer"><div class="footer-name">NORVALE<small>NEUROLABS</small></div></footer>
</section>

<!-- Bar Chart -->
<section class="slide" style="left:423px; top:440px;">
  <h2 class="slide__title">Bar Chart</h2>
  <svg class="chart" viewBox="0 0 333 250">
    <g font-size="5.5" text-anchor="end">
      <text x="62" y="189">0</text><text x="62" y="173">1</text><text x="62" y="157">2</text>
      <text x="62" y="141">3</text><text x="62" y="125">4</text><text x="62" y="109">5</text>
      <text x="62" y="93">6</text><text x="62" y="77">7</text>
    </g>
    <line x1="66" y1="187" x2="254" y2="187" stroke="#999" stroke-width=".6"/>
    <g>
      <rect x="75" y="118.2" width="7" height="68.8" fill="var(--brand-mid)"/>
      <rect x="82" y="148.6" width="7" height="38.4" fill="var(--brand-light)"/>
      <rect x="89" y="155" width="7" height="32" fill="var(--brand-dark)"/>
      <rect x="96" y="107" width="7" height="80" fill="var(--brand-bright)"/>

      <rect x="121" y="147" width="7" height="40" fill="var(--brand-mid)"/>
      <rect x="128" y="116.6" width="7" height="70.4" fill="var(--brand-light)"/>
      <rect x="135" y="139" width="7" height="48" fill="var(--brand-dark)"/>
      <rect x="142" y="126.2" width="7" height="60.8" fill="var(--brand-bright)"/>

      <rect x="167" y="131" width="7" height="56" fill="var(--brand-mid)"/>
      <rect x="174" y="158.2" width="7" height="28.8" fill="var(--brand-light)"/>
      <rect x="181" y="91" width="7" height="96" fill="var(--brand-dark)"/>
      <rect x="188" y="142.2" width="7" height="44.8" fill="var(--brand-bright)"/>

      <rect x="213" y="115" width="7" height="72" fill="var(--brand-mid)"/>
      <rect x="220" y="142.2" width="7" height="44.8" fill="var(--brand-light)"/>
      <rect x="227" y="107" width="7" height="80" fill="var(--brand-dark)"/>
      <rect x="234" y="135.8" width="7" height="51.2" fill="var(--brand-bright)"/>
    </g>
    <g font-size="5" text-anchor="middle">
      <text x="78.5" y="115">4.3</text><text x="85.5" y="146">2.4</text><text x="92.5" y="152">2</text><text x="99.5" y="104">5</text>
      <text x="124.5" y="144">2.5</text><text x="131.5" y="114">4.4</text><text x="138.5" y="136">3</text><text x="145.5" y="123">3.8</text>
      <text x="170.5" y="128">3.5</text><text x="177.5" y="155">1.8</text><text x="184.5" y="88">6</text><text x="191.5" y="139">2.8</text>
      <text x="216.5" y="112">4.5</text><text x="223.5" y="139">2.8</text><text x="230.5" y="104">5</text><text x="237.5" y="133">3.2</text>
    </g>
    <g font-size="6" text-anchor="middle">
      <text x="89" y="197">A</text><text x="135" y="197">B</text><text x="181" y="197">C</text><text x="227" y="197">D</text>
    </g>
    <g font-size="5.5">
      <rect x="263" y="116" width="3" height="3" fill="var(--brand-mid)"/><text x="268" y="119.5">S1</text>
      <rect x="263" y="125" width="3" height="3" fill="var(--brand-light)"/><text x="268" y="128.5">S2</text>
      <rect x="263" y="134" width="3" height="3" fill="var(--brand-dark)"/><text x="268" y="137.5">S3</text>
      <rect x="263" y="143" width="3" height="3" fill="var(--brand-bright)"/><text x="268" y="146.5">S4</text>
    </g>
  </svg>
  <footer class="slide__footer"><div class="footer-name">NORVALE<small>NEUROLABS</small></div></footer>
</section>

<!-- Line Chart -->
<section class="slide" style="left:825px; top:440px;">
  <h2 class="slide__title">Line Chart</h2>
  <svg class="chart" viewBox="0 0 333 250">
    <g font-size="5" text-anchor="end">
      <text x="34" y="187">0</text><text x="34" y="174">0.5</text><text x="34" y="161">1</text>
      <text x="34" y="149">1.5</text><text x="34" y="136">2</text><text x="34" y="123">2.5</text>
      <text x="34" y="110">3</text><text x="34" y="97">3.5</text><text x="34" y="84">4</text>
      <text x="34" y="72">4.5</text><text x="34" y="59">5</text>
    </g>
    <line x1="40" y1="185" x2="235" y2="185" stroke="#999" stroke-width=".6"/>
    <g fill="none" stroke-width="1.2">
      <polyline points="69,75 117,121 167,95.4 216,69.8" stroke="var(--brand-light)"/>
      <polyline points="69,123.6 117,72.4 167,138.9 216,113.3" stroke="var(--brand-dark)"/>
      <polyline points="69,159.4 117,154.3 167,118.4 216,146.6" stroke="var(--brand-mid)"/>
      <polyline points="69,174.8 117,98 167,69.8 216,90.3" stroke="#6a9bd2"/>
    </g>
    <g>
      <circle cx="69" cy="75" r="1.6" fill="var(--brand-light)"/><circle cx="117" cy="121" r="1.6" fill="var(--brand-light)"/>
      <circle cx="167" cy="95.4" r="1.6" fill="var(--brand-light)"/><circle cx="216" cy="69.8" r="1.6" fill="var(--brand-light)"/>
      <circle cx="69" cy="123.6" r="1.6" fill="var(--brand-dark)"/><circle cx="117" cy="72.4" r="1.6" fill="var(--brand-dark)"/>
      <circle cx="167" cy="138.9" r="1.6" fill="var(--brand-dark)"/><circle cx="216" cy="113.3" r="1.6" fill="var(--brand-dark)"/>
      <circle cx="69" cy="159.4" r="1.6" fill="var(--brand-mid)"/><circle cx="117" cy="154.3" r="1.6" fill="var(--brand-mid)"/>
      <circle cx="167" cy="118.4" r="1.6" fill="var(--brand-mid)"/><circle cx="216" cy="146.6" r="1.6" fill="var(--brand-mid)"/>
      <circle cx="69" cy="174.8" r="1.6" fill="#6a9bd2"/><circle cx="117" cy="98" r="1.6" fill="#6a9bd2"/>
      <circle cx="167" cy="69.8" r="1.6" fill="#6a9bd2"/><circle cx="216" cy="90.3" r="1.6" fill="#6a9bd2"/>
    </g>
    <g font-size="5" text-anchor="middle">
      <text x="69" y="71">4.3</text><text x="117" y="128">2.5</text><text x="167" y="91">3.5</text><text x="216" y="66">4.5</text>
      <text x="69" y="119">2.4</text><text x="117" y="68">4.4</text><text x="167" y="146">1.8</text><text x="216" y="109">2.8</text>
      <text x="69" y="155">1</text><text x="117" y="150">1.2</text><text x="167" y="114">2.6</text><text x="216" y="142">1.5</text>
      <text x="69" y="170">0.4</text><text x="117" y="93" font-weight="700">3.4</text><text x="167" y="64" font-weight="700">4.5</text><text x="216" y="85" font-weight="700">3.7</text>
    </g>
    <g font-size="4.8" text-anchor="middle">
      <text x="69" y="193">Category 1</text><text x="117" y="193">Category 2</text>
      <text x="167" y="193">Category 3</text><text x="216" y="193">Category 4</text>
    </g>
    <g font-size="4.8">
      <line x1="250" y1="143" x2="257" y2="143" stroke="var(--brand-light)"/><text x="259" y="145">Series 1</text>
      <line x1="250" y1="151" x2="257" y2="151" stroke="var(--brand-dark)"/><text x="259" y="153">Series 2</text>
      <line x1="250" y1="159" x2="257" y2="159" stroke="var(--brand-mid)"/><text x="259" y="161">Series 3</text>
      <line x1="250" y1="167" x2="257" y2="167" stroke="#6a9bd2"/><text x="259" y="169">Series 4</text>
    </g>
  </svg>
  <footer class="slide__footer"><div class="footer-name">NORVALE<small>NEUROLABS</small></div></footer>
</section>

<!-- Table -->
<section class="slide" style="left:25px; top:735px;">
  <h2 class="slide__title">Table</h2>
  <table class="data-table">
    <thead>
      <tr><th>Title A</th><th>Title B</th><th>Title C</th><th>Title D</th><th>Title E</th></tr>
    </thead>
    <tbody>
      <tr><td>Text here</td><td>1234567890</td><td>1234567890</td><td>1234567890</td><td>1234567890</td></tr>
      <tr><td>Text here</td><td>1234567890</td><td>1234567890</td><td>1234567890</td><td>1234567890</td></tr>
      <tr><td>Text here</td><td>1234567890</td><td>1234567890</td><td>1234567890</td><td>1234567890</td></tr>
      <tr><td>Text here</td><td>1234567890</td><td>1234567890</td><td>1234567890</td><td>1234567890</td></tr>
      <tr><td>Text here</td><td>1234567890</td><td>1234567890</td><td>1234567890</td><td>1234567890</td></tr>
      <tr><td>Text here</td><td>1234567890</td><td>1234567890</td><td>1234567890</td><td>1234567890</td></tr>
      <tr><td>Text here</td><td>1234567890</td><td>1234567890</td><td>1234567890</td><td>1234567890</td></tr>
      <tr><td>Text here</td><td>1234567890</td><td>1234567890</td><td>1234567890</td><td>1234567890</td></tr>
    </tbody>
  </table>
  <footer class="slide__footer"><div class="footer-name">NORVALE<small>NEUROLABS</small></div></footer>
</section>

<!-- Blank -->
<section class="slide" style="left:423px; top:735px;">
  <div class="blank-label">BLANK</div>
  <footer class="slide__footer"><div class="footer-name">NORVALE<small>NEUROLABS</small></div></footer>
</section>

<!-- Closing -->
<section class="slide slide--brand" style="left:817px; top:733px;">
  <div class="cover-name">NORVALE<small>NEUROLABS</small></div>
  <div class="cover-heading">Thank You</div>
  <div class="cover-date">October 26, 2013</div>
</section>

</body>
</html>
```